Professional & attention grabbing.

A business card design, front and back. I already have a logo I will attach, but I am open to something new as well.
Things to include:
Name:
Title:
Phone:
Email:
Wanting something that is professional but attention grabbing.
Also we do a lot of work using drones on natural gas pipelines (leading the future)if you want to include any of that. I'm open to ideas.
Target Market(s)
Natural gas transmission industry / greenhouse gas mitigation industry
Industry/Entity Type
Business
Colors
Designer to choose colors to be used in the design.
Look and feel
Each slider illustrates characteristics of the customer's brand and the style your logo design should communicate.

```html
<!DOCTYPE html>
<html lang="en">
<head>
<meta charset="UTF-8">
<title>Kestrel Inspections — Business Card</title>
<link href="https://fonts.googleapis.com/css2?family=Montserrat:wght@500;600;700&display=swap" rel="stylesheet">
<style>
  :root {
    --canvas-bg: #d9d9d9;
    --card-white: #ffffff;
    --brand-red: #c8202a;
    --charcoal: #3a3a3c;
    --text-light: #ffffff;
  }
  * { margin: 0; padding: 0; box-sizing: border-box; }
  html, body { width: 1200px; height: 1000px; overflow: hidden; }
  body {
    background: var(--canvas-bg);
    font-family: "Montserrat", Arial, sans-serif;
    position: relative;
  }
  .card {
    position: absolute;
    top: 345px;
    width: 540px;
    height: 310px;
    background: var(--card-white);
    overflow: hidden;
    box-shadow: 0 4px 14px rgba(0,0,0,0.18);
  }
  .card--back { left: 40px; }
  .card--front { left: 620px; }

  .brand {
    position: absolute;
    display: flex;
    align-items: center;
    gap: 12px;
    color: var(--charcoal);
    font-weight: 700;
    letter-spacing: 0.5px;
    white-space: nowrap;
  }
  .brand__mark { background: var(--brand-red); }
  .card--back .brand { top: 46px; left: 50%; transform: translateX(-50%); font-size: 30px; }
  .card--back .brand__mark { width: 30px; height: 30px; }
  .card--front .brand { top: 50%; left: 50%; transform: translate(-50%, -60%); font-size: 34px; }
  .card--front .brand__mark { width: 34px; height: 34px; }

  .back-swoosh { position: absolute; inset: 0; width: 540px; height: 310px; }
  .back-swoosh .swoosh-red { fill: var(--brand-red); }
  .back-swoosh .swoosh-dark { fill: var(--charcoal); }

  .contact-block {
    position: absolute;
    top: 232px;
    left: 0;
    width: 540px;
    display: flex;
    justify-content: center;
    align-items: center;
    gap: 14px;
  }
  .person { text-align: right; }
  .person__name { color: var(--brand-red); font-weight: 600; font-size: 19px; letter-spacing: 0.3px; }
  .person__title { color: var(--text-light); font-weight: 700; font-size: 13px; margin-top: 3px; }
  .divider { width: 1.5px; height: 46px; background: var(--text-light); }
  .details { display: flex; flex-direction: column; gap: 7px; }
  .details__row { display: flex; align-items: center; gap: 8px; color: var(--text-light); font-size: 12px; font-weight: 500; }
  .details__icon { width: 15px; height: 15px; }
  .details__icon rect { fill: var(--brand-red); }
  .details__icon path { fill: none; stroke: var(--text-light); stroke-width: 1.4; stroke-linejoin: round; stroke-linecap: round; }

  .front-strip { position: absolute; left: 0; bottom: 0; width: 100%; height: 12px; display: flex; }
  .front-strip__red { flex: 1; background: var(--brand-red); }
  .front-strip__dark { flex: 1; background: var(--charcoal); }
</style>
</head>
<body>
  <section class="card card--back" aria-label="Card back">
    <div class="brand"><span class="brand__mark"></span>KESTREL INSPECTIONS</div>
    <svg class="back-swoosh" viewBox="0 0 540 310" aria-hidden="true">
      <path class="swoosh-red" d="M0,192 Q270,112 540,162 L540,172 Q270,128 0,206 Z"/>
      <path class="swoosh-dark" d="M0,212 Q270,136 540,178 L540,310 L0,310 Z"/>
    </svg>
    <div class="contact-block">
      <div class="person">
        <div class="person__name">DANIEL ARCHER</div>
        <div class="person__title">FOUNDER</div>
      </div>
      <div class="divider"></div>
      <div class="details">
        <div class="details__row">
          <svg class="details__icon" viewBox="0 0 15 15" aria-hidden="true"><rect width="15" height="15" rx="2"/><path d="M4.5,3.5 L6.2,3.5 L6.8,5.8 L5.8,6.6 Q6.9,8.6 8.4,9.2 L9.2,8.2 L11.5,8.8 L11.5,10.5 Q7.5,11.5 4.5,3.5 Z"/></svg>
          <span>000 000 0000</span>
        </div>
        <div class="details__row">
          <svg class="details__icon" viewBox="0 0 15 15" aria-hidden="true"><rect width="15" height="15" rx="2"/><path d="M3.5,4.5 H11.5 V10.5 H3.5 Z M3.5,4.5 L7.5,8 L11.5,4.5"/></svg>
          <span>info@kestrelinspect.com</span>
        </div>
      </div>
    </div>
  </section>

  <section class="card card--front" aria-label="Card front">
    <div class="brand"><span class="brand__mark"></span>KESTREL INSPECTIONS</div>
    <div class="front-strip"><span class="front-strip__red"></span><span class="front-strip__dark"></span></div>
  </section>
</body>
</html>
```